Website re-design for Brightmoor LLC website ( has existing website )

Looking to do a complete re-design of Brightmoorllc. The existing website is dated and built in wordpress. The new website will not be wordpress. The project folder includes an overview.txt file with details on the project. The file also contains a list of websites that he/she likes which I am sure is very helpful .
Number of Pages Required
1 page

```html
<!DOCTYPE html>
<html lang="en">
<head>
<meta charset="utf-8">
<title>Brightmoor LLC — Shoreline Services</title>
<link href="https://fonts.googleapis.com/css2?family=Lexend:wght@400;500;600&family=Barlow:ital,wght@0,400;0,500;0,600;1,400&display=swap" rel="stylesheet">
<style>
:root{
  --blue:#1a73c8;
  --navy:#0c2d4f;
  --orange:#ff7a12;
  --ink:#222a33;
  --muted:#5b6570;
  --line:#d5dde6;
  --white:#ffffff;
}
*{box-sizing:border-box;margin:0;padding:0}
html,body{width:1200px;height:4307px;overflow:hidden}
body{position:relative;background:var(--white);font-family:"Barlow",sans-serif;color:var(--ink)}
.abs{position:absolute}
.head{font-family:"Lexend",sans-serif}
.btn{position:absolute;display:flex;align-items:center;justify-content:center;border-radius:30px;font-family:"Barlow",sans-serif;font-weight:600;font-size:13px;letter-spacing:.3px;text-transform:uppercase}
.btn-blue{background:var(--blue);color:var(--white)}
.btn-orange{background:var(--orange);color:var(--white)}
.btn-outline{border:2px solid var(--blue);color:var(--blue);background:var(--white)}
.underline{position:absolute;height:3px;background:var(--blue);width:46px}
.underline::after{content:"";position:absolute;left:8px;right:8px;top:7px;height:2px;background:var(--blue)}

/* header */
.site-header{position:absolute;left:0;top:0;width:1200px;height:90px;background:var(--white)}
.brand{position:absolute;display:flex;align-items:center;gap:12px}
.brand-mark{width:22px;height:22px;background:var(--blue)}
.brand-name{font-family:"Barlow",sans-serif;font-size:30px;font-weight:500;color:var(--ink);line-height:1}
.nav{position:absolute;top:34px;left:0;font-size:16px;color:var(--ink)}
.nav span{position:absolute;white-space:nowrap}
.nav .active{color:var(--blue)}
.nav-bar{position:absolute;left:386px;top:86px;width:95px;height:3px;background:var(--blue)}

/* hero */
.hero{position:absolute;left:0;top:90px;width:1200px;height:600px;background:linear-gradient(160deg,#6b6a3c 0%,#4f5a3e 35%,#3e4d45 60%,#5c6a58 100%)}
.hero-eyebrow{left:100px;top:233px;color:var(--white);font-size:22px;letter-spacing:2.5px;font-family:"Lexend",sans-serif;font-weight:400}
.hero-title{left:100px;top:262px;color:var(--white);font-family:"Lexend",sans-serif;font-weight:600;font-size:50px;line-height:52px;text-transform:uppercase;letter-spacing:-1px}
.arrow{position:absolute}

/* about */
.media{position:absolute;background:linear-gradient(180deg,#3c3a44 0%,#8a5a48 38%,#e88a3a 46%,#2e2a2c 62%,#4a3a32 100%)}
.about-title{left:628px;top:752px;font-size:32px;line-height:38px;font-weight:500;color:var(--ink)}
.about-copy{left:632px;top:857px;width:485px;font-size:16px;line-height:27px;color:#3b444d}

/* services */
.services-bg{position:absolute;left:0;top:1192px;width:1200px;height:1100px;background:linear-gradient(180deg,#e6eff8 0%,#dde9f5 50%,#cfe2f3 100%)}
.section-title{position:absolute;left:0;width:1200px;text-align:center;font-family:"Lexend",sans-serif;font-weight:400;font-size:31px;color:var(--ink)}
.card{position:absolute;width:320px;height:403px;background:var(--white);text-align:center}
.card.featured{background:var(--blue)}
.card .pic{height:221px}
.card h3{font-family:"Lexend",sans-serif;font-weight:500;font-size:17px;line-height:21px;color:var(--ink);margin-top:22px;text-transform:uppercase}
.card.featured h3{color:var(--white)}
.card p{font-size:13px;line-height:19px;color:var(--muted);padding:0 30px;margin-top:6px}
.card.featured p{color:#d7e8f8}
.card .btn{left:91px;width:138px;height:36px;font-size:11px}
.card.featured .btn{border-color:var(--white);color:var(--white);background:transparent}

/* gallery */
.shot{position:absolute}

/* testimonials */
.testi-bg{position:absolute;left:0;top:2855px;width:1200px;height:540px;background:linear-gradient(180deg,#2f8fe2 0%,#1e7ad4 55%,#3a96e4 100%)}
.quote-card{position:absolute;left:285px;top:3032px;width:608px;height:238px;background:var(--white);border-radius:4px;text-align:center}
.quote-text{margin:58px auto 0;width:500px;font-style:italic;font-size:17px;line-height:22px;color:var(--ink)}
.quote-name{font-family:"Lexend",sans-serif;font-size:14px;margin-top:24px;color:var(--ink)}
.quote-sub{font-family:"Lexend",sans-serif;font-size:12px;margin-top:6px;color:var(--ink)}

/* contact */
.contact-bg{position:absolute;left:0;top:3390px;width:1200px;height:530px;background:linear-gradient(180deg,#ffffff 0%,#f2f7fb 40%,#dfe9f1 100%)}
.call-pill{position:absolute;left:450px;top:3530px;width:317px;height:56px;border-radius:30px;background:var(--white);border:1px solid var(--line);display:flex;align-items:center;padding-left:10px;gap:10px}
.call-icon{width:38px;height:38px;border-radius:50%;background:var(--blue);display:flex;align-items:center;justify-content:center}
.call-label{font-size:14px;color:var(--muted)}
.call-number{font-size:20px;color:var(--ink);font-weight:500}
.field{position:absolute;background:var(--white);border:1px solid var(--line);font-size:13px;color:var(--ink);display:flex;align-items:center;gap:8px;padding-left:18px}
.field.message{align-items:flex-start;padding-top:10px}

/* footer */
.foot-text{font-size:12px;line-height:19px;color:var(--muted)}
.foot-head{font-family:"Barlow",sans-serif;font-weight:600;font-size:18px;color:var(--ink)}
.foot-link{position:absolute;font-size:13px;color:var(--muted)}
.foot-rule{position:absolute;width:2px;height:24px;background:var(--blue)}
.social{position:absolute;width:28px;height:28px;border-radius:50%;background:var(--blue)}
</style>
</head>
<body>

<!-- Header -->
<header class="site-header">
  <div class="brand" style="left:70px;top:29px">
    <div class="brand-mark"></div>
    <div class="brand-name">Brightmoor</div>
  </div>
  <nav class="nav">
    <span class="active" style="left:398px">Services</span>
    <span style="left:498px">About Us</span>
    <span style="left:600px">FAQs</span>
    <span style="left:675px">Employment</span>
    <span style="left:802px">Testimonials</span>
    <span style="left:927px">Gallery</span>
  </nav>
  <div class="nav-bar"></div>
  <div class="btn btn-blue" style="left:1008px;top:27px;width:137px;height:39px;font-size:15px;font-weight:500;text-transform:none">Contact Us</div>
</header>

<!-- Hero -->
<section class="hero" role="img" aria-label="Photo of clear lake water over weeds with a boat motor in the corner"></section>
<svg class="abs" style="left:0;top:600px" width="1200" height="100" viewBox="0 0 1200 100" aria-hidden="true">
  <path d="M0 40 C120 10 220 80 380 70 C560 58 640 30 820 45 C980 58 1080 5 1200 50 L1200 100 L0 100 Z" fill="#ffffff"/>
</svg>
<div class="abs hero-eyebrow">WELCOME TO BRIGHTMOOR</div>
<h1 class="abs hero-title">We know there<br>is no life like<br>the lake life</h1>
<div class="btn btn-orange" style="left:105px;top:430px;width:170px;height:45px">Free Estimate</div>
<svg class="arrow" style="left:14px;top:342px" width="28" height="52" viewBox="0 0 28 52" aria-hidden="true"><path d="M24 2 L4 26 L24 50" fill="none" stroke="#fff" stroke-width="3"/></svg>
<svg class="arrow" style="left:1136px;top:342px" width="28" height="52" viewBox="0 0 28 52" aria-hidden="true"><path d="M4 2 L24 26 L4 50" fill="none" stroke="#fff" stroke-width="3"/></svg>

<!-- About -->
<div class="media" style="left:107px;top:752px;width:477px;height:326px" role="img" aria-label="Video still of a sunset over a lake seen from a wooden dock"></div>
<svg class="abs" style="left:312px;top:877px" width="66" height="66" viewBox="0 0 66 66" aria-hidden="true">
  <circle cx="33" cy="33" r="30" fill="none" stroke="#fff" stroke-width="4"/>
  <path d="M26 20 L47 33 L26 46 Z" fill="#fff"/>
</svg>
<h2 class="abs head about-title">Aquatic Innovators,<br>at Your Service.</h2>
<div class="underline" style="left:665px;top:833px"></div>
<p class="abs about-copy">Brightmoor LLC is a company formed in response to the increasing incidence of invasive species in Minnesota's lakes and water systems. The impact of these fast-growing nuisances, inspired our venture to effectively control unwanted lake weeds. Brightmoor LLC helps provide the enjoyable weed-free lake environment craved by water enthusiasts.</p>
<div class="btn btn-blue" style="left:632px;top:1038px;width:148px;height:43px">Learn More</div>

<!-- Services -->
<div class="services-bg" role="img" aria-label="Faint background photo of pine trees and a snowy lakeshore"></div>
<svg class="abs" style="left:0;top:2260px" width="1200" height="60" viewBox="0 0 1200 60" aria-hidden="true">
  <path d="M0 30 C80 10 150 45 260 35 C380 25 420 5 560 20 C700 35 760 10 880 22 C1000 35 1100 12 1200 28 L1200 60 L0 60 Z" fill="#ffffff"/>
</svg>
<h2 class="section-title" style="top:1245px">Dock Install and Removal Services</h2>
<div class="underline" style="left:577px;top:1297px"></div>

<div class="card featured" style="left:107px;top:1337px">
  <div class="pic" style="background:linear-gradient(135deg,#6a6a55 0%,#b88a4a 55%,#4c4a3c 100%)" role="img" aria-label="Close-up of zebra mussels on a rock"></div>
  <h3>Zebra Mussel Removal</h3>
  <p>Lorem Ipsum is simply dummy text of the printing and typesetting industry. Lorem Ipsum has been the industry's</p>
  <div class="btn btn-outline" style="top:345px">Learn More</div>
</div>
<div class="card" style="left:437px;top:1337px">
  <div class="pic" style="background:linear-gradient(180deg,#8fc3ea 0%,#e8eef2 45%,#3a8fc4 70%,#d9c9a6 100%)" role="img" aria-label="White canopy cabana on a sunny beach"></div>
  <h3>Canopy Services</h3>
  <p>Lorem Ipsum is simply dummy text of the printing and typesetting industry. Lorem Ipsum has been the industry's</p>
  <div class="btn btn-outline" style="top:345px">Learn More</div>
</div>
<div class="card" style="left:769px;top:1337px">
  <div class="pic" style="background:linear-gradient(180deg,#9fc4e6 0%,#c9d6de 40%,#8b8e90 65%,#6b6c58 100%)" role="img" aria-label="Work barge on a trailer beside a truck"></div>
  <h3>Barge Services<br>(Fall 2022)</h3>
  <p>Lorem Ipsum is simply dummy text of the printing and typesetting industry</p>
  <div class="btn btn-outline" style="top:340px">Learn More</div>
</div>
<div class="card" style="left:111px;top:1765px">
  <div class="pic" style="background:linear-gradient(180deg,#2a6fd0 0%,#bcd8f2 40%,#e4e8ec 60%,#2b5d8e 100%)" role="img" aria-label="Boat lifts with canopies on a lake under blue sky"></div>
  <h3>Dock Lift Services<br>(Fall 2022)</h3>
  <p>Lorem Ipsum is simply dummy text of the printing and typesetting industry</p>
  <div class="btn btn-outline" style="top:340px">Learn More</div>
</div>
<div class="card" style="left:441px;top:1765px">
  <div class="pic" style="background:linear-gradient(160deg,#5b8a3a,#3f6a2e 50%,#6f8f40)" role="img" aria-label="Divers working among lily pads"></div>
  <h3>Aquatic Weed<br>Removal</h3>
  <p>Lorem Ipsum is simply dummy text of the printing and typesetting industry</p>
  <div class="btn btn-outline" style="top:340px">Learn More</div>
</div>
<div class="card" style="left:771px;top:1765px">
  <div class="pic" style="background:linear-gradient(160deg,#c9b9a0,#a8987c 50%,#d6c8b2)" role="img" aria-label="Volunteer picking up litter on a sandy beach"></div>
  <h3>Beach Clean<br>Up Services</h3>
  <p>Lorem Ipsum is simply dummy text of the printing and typesetting industry</p>
  <div class="btn btn-outline" style="top:340px">Learn More</div>
</div>
<div class="btn btn-blue" style="left:492px;top:2200px;width:225px;height:50px;font-size:15px">View All Services</div>

<!-- Gallery -->
<h2 class="section-title" style="top:2350px">Before &amp; After Gallery</h2>
<div class="underline" style="left:577px;top:2402px"></div>
<div class="shot" style="left:112px;top:2485px;width:251px;height:240px;background:linear-gradient(180deg,#7fb2e2 0%,#bcd3e6 35%,#2d5f8e 60%,#a59f94 100%)" role="img" aria-label="Before photo of a dock with boat lift"></div>
<div class="shot" style="left:363px;top:2452px;width:240px;height:305px;background:linear-gradient(180deg,#dfe6d8 0%,#6f8f4a 30%,#7b7a66 75%,#a39a8a 100%)" role="img" aria-label="Before photo of a weedy dock path"></div>
<div class="shot" style="left:603px;top:2452px;width:239px;height:305px;background:linear-gradient(180deg,#c8d5b8 0%,#3e6a2c 30%,#6b8e44 60%,#b2a791 100%)" role="img" aria-label="After photo of a cleared dock path"></div>
<div class="shot" style="left:842px;top:2493px;width:226px;height:240px;background:linear-gradient(90deg,#6b7e4a 0%,#8d9a62 20%,#4f6c4e 40%,#7b8e6a 100%)" role="img" aria-label="After photo of clear shoreline water"></div>
<svg class="abs" style="left:572px;top:2582px" width="52" height="52" viewBox="0 0 52 52" aria-hidden="true">
  <circle cx="26" cy="26" r="23" fill="none" stroke="#fff" stroke-width="3"/>
  <path d="M22 17 L13 26 L22 35 Z M30 17 L39 26 L30 35 Z" fill="#fff"/>
</svg>
<svg class="arrow" style="left:58px;top:2588px" width="26" height="48" viewBox="0 0 26 48" aria-hidden="true"><path d="M22 2 L4 24 L22 46" fill="none" stroke="#8a939c" stroke-width="3"/></svg>
<svg class="arrow" style="left:1088px;top:2588px" width="26" height="48" viewBox="0 0 26 48" aria-hidden="true"><path d="M4 2 L22 24 L4 46" fill="none" stroke="#8a939c" stroke-width="3"/></svg>

<!-- Testimonials -->
<div class="testi-bg" role="img" aria-label="Blue-tinted photo of a pine forest by the water"></div>
<svg class="abs" style="left:0;top:3340px" width="1200" height="60" viewBox="0 0 1200 60" aria-hidden="true">
  <path d="M0 35 C120 10 220 40 360 30 C520 20 600 45 760 28 C920 12 1040 40 1200 20 L1200 60 L0 60 Z" fill="#ffffff"/>
</svg>
<h2 class="section-title" style="top:2925px;color:#fff;font-size:34px">Testimonials</h2>
<div class="underline" style="left:577px;top:2978px;background:#fff"></div>
<div class="quote-card">
  <p class="quote-text">Everyone used to jump off the water trampoline and instantly get tangled in lake weeds. We contacted Brightmoor and their SCUBA divers have now been solving our problem for the past 4 years!"</p>
  <div class="quote-name">Pine Hollow Shore Association</div>
  <div class="quote-sub">(Lake Minnetonka)</div>
</div>
<svg class="abs" style="left:560px;top:3005px" width="54" height="54" viewBox="0 0 54 54" aria-hidden="true">
  <circle cx="27" cy="27" r="26" fill="#1a73c8"/>
  <path d="M17 30 a5 5 0 1 0 5 -5 q0 -5 4 -7 M29 30 a5 5 0 1 0 5 -5 q0 -5 4 -7" fill="none" stroke="#fff" stroke-width="3"/>
</svg>
<svg class="arrow" style="left:188px;top:3115px" width="26" height="48" viewBox="0 0 26 48" aria-hidden="true"><path d="M22 2 L4 24 L22 46" fill="none" stroke="#fff" stroke-width="3"/></svg>
<svg class="arrow" style="left:945px;top:3115px" width="26" height="48" viewBox="0 0 26 48" aria-hidden="true"><path d="M4 2 L22 24 L4 46" fill="none" stroke="#fff" stroke-width="3"/></svg>

<!-- Contact -->
<div class="contact-bg" role="img" aria-label="Faint photo of a calm lake with pines"></div>
<h2 class="section-title" style="top:3450px;font-size:34px">Leave Message or Call Us Now</h2>
<div class="underline" style="left:577px;top:3505px"></div>
<div class="call-pill">
  <div class="call-icon">
    <svg width="18" height="18" viewBox="0 0 24 24" aria-hidden="true"><path d="M6.6 10.8a15.1 15.1 0 0 0 6.6 6.6l2.2-2.2a1 1 0 0 1 1-.25 11.4 11.4 0 0 0 3.6.57 1 1 0 0 1 1 1V20a1 1 0 0 1-1 1A17 17 0 0 1 3 4a1 1 0 0 1 1-1h3.5a1 1 0 0 1 1 1c0 1.25.2 2.45.57 3.6a1 1 0 0 1-.25 1z" fill="#fff"/></svg>
  </div>
  <span class="call-label">CALL US NOW</span>
  <span class="call-number">(612) 555-0148</span>
</div>
<div class="field" style="left:207px;top:3625px;width:405px;height:45px">
  <svg width="14" height="14" viewBox="0 0 24 24" aria-hidden="true"><circle cx="12" cy="8" r="5" fill="#8a939c"/><path d="M3 22c0-5 4-8 9-8s9 3 9 8z" fill="#8a939c"/></svg>Your Name</div>
<div class="field" style="left:207px;top:3680px;width:405px;height:44px">
  <svg width="14" height="14" viewBox="0 0 24 24" aria-hidden="true"><path d="M6.6 10.8a15.1 15.1 0 0 0 6.6 6.6l2.2-2.2a1 1 0 0 1 1-.25 11.4 11.4 0 0 0 3.6.57 1 1 0 0 1 1 1V20a1 1 0 0 1-1 1A17 17 0 0 1 3 4a1 1 0 0 1 1-1h3.5a1 1 0 0 1 1 1c0 1.25.2 2.45.57 3.6a1 1 0 0 1-.25 1z" fill="#8a939c"/></svg>Phone number</div>
<div class="field" style="left:207px;top:3735px;width:405px;height:45px">
  <svg width="14" height="14" viewBox="0 0 24 24" aria-hidden="true"><rect x="2" y="5" width="20" height="14" fill="none" stroke="#8a939c" stroke-width="2"/><path d="M2 5l10 8 10-8" fill="none" stroke="#8a939c" stroke-width="2"/></svg>Email address</div>
<div class="field message" style="left:626px;top:3625px;width:405px;height:155px">Message</div>
<div class="btn btn-orange" style="left:530px;top:3800px;width:191px;height:55px;font-size:15px;font-weight:500">Send Enquiry</div>

<!-- Footer -->
<footer>
  <div class="brand" style="left:117px;top:3990px">
    <div class="brand-mark" style="width:20px;height:20px"></div>
    <div class="brand-name" style="font-size:28px">Brightmoor</div>
  </div>
  <p class="abs foot-text" style="left:122px;top:4047px;width:300px">Brightmoor LLC is a company formed in response to the increasing incidence of invasive species in Minnesota's lakes and water systems.</p>
  <div class="social" style="left:123px;top:4123px"></div>
  <div class="social" style="left:163px;top:4123px"></div>
  <div class="social" style="left:204px;top:4123px"></div>
  <div class="social" style="left:244px;top:4123px"></div>

  <div class="foot-rule" style="left:492px;top:3982px"></div>
  <div class="abs foot-head" style="left:515px;top:3982px">QUICK LINKS</div>
  <span class="foot-link" style="left:518px;top:4025px">Home</span>
  <span class="foot-link" style="left:518px;top:4056px">Services</span>
  <span class="foot-link" style="left:518px;top:4087px">About Us</span>
  <span class="foot-link" style="left:518px;top:4118px">Contact Us</span>
  <span class="foot-link" style="left:655px;top:4025px">FAQs</span>
  <span class="foot-link" style="left:655px;top:4056px">Employment</span>
  <span class="foot-link" style="left:655px;top:4087px">Testimonials</span>
  <span class="foot-link" style="left:655px;top:4118px">Gallery</span>

  <div class="foot-rule" style="left:838px;top:3982px"></div>
  <div class="abs foot-head" style="left:866px;top:3982px">CONTACT US</div>
  <svg class="abs" style="left:866px;top:4025px" width="24" height="24" viewBox="0 0 24 24" aria-hidden="true"><circle cx="12" cy="12" r="12" fill="#e8eef4"/><path d="M12 5a4 4 0 0 0-4 4c0 3 4 9 4 9s4-6 4-9a4 4 0 0 0-4-4z" fill="#0c2d4f"/><circle cx="12" cy="9" r="1.5" fill="#e8eef4"/></svg>
  <p class="abs foot-text" style="left:904px;top:4023px">4418 Birchwood Trail<br>Lakeview, MN 55000</p>
  <svg class="abs" style="left:866px;top:4075px" width="24" height="24" viewBox="0 0 24 24" aria-hidden="true"><circle cx="12" cy="12" r="12" fill="#e8eef4"/><rect x="6" y="8" width="12" height="8" fill="none" stroke="#0c2d4f" stroke-width="1.5"/><path d="M6 8l6 5 6-5" fill="none" stroke="#0c2d4f" stroke-width="1.5"/></svg>
  <span class="foot-link" style="left:904px;top:4079px;font-size:12px">hello@brightmoor-example.com</span>
  <svg class="abs" style="left:866px;top:4110px" width="24" height="24" viewBox="0 0 24 24" aria-hidden="true"><circle cx="12" cy="12" r="12" fill="#e8eef4"/><path d="M8.5 10.8a9 9 0 0 0 4.7 4.7l1.4-1.4a.7.7 0 0 1 .7-.2 7 7 0 0 0 2.1.35.7.7 0 0 1 .6.6V17a.7.7 0 0 1-.6.7A11 11 0 0 1 6.3 6.6a.7.7 0 0 1 .7-.6h2.1a.7.7 0 0 1 .6.6 7 7 0 0 0 .35 2.1.7.7 0 0 1-.2.7z" fill="#0c2d4f"/></svg>
  <span class="foot-link" style="left:904px;top:4113px;font-size:14px">(612) 555-0148</span>

  <div class="abs" style="left:104px;top:4232px;width:1026px;height:1px;background:var(--line)"></div>
  <div class="abs" style="left:0;top:4252px;width:1200px;text-align:center;font-size:11px;color:var(--muted)">Copyright: 2022 Brightmoor LLC</div>
</footer>

</body>
</html>
```